Redesign of business card for Cedar Ridge Mechanical

We are looking for a new design for our business cards for Cedar Ridge Mechanical. We are a plumbing & HVAC construction company, operating on the West Coast of Canada and USA. Logo attached.
Industry/Entity Type
Construction - Plumbing & HVAC
Contact Information for Business Card
Name, address, phone numbers, email, website address
Look and feel
Each slider illustrates characteristics of the customer's brand and the style your logo design should communicate.

```html
<!DOCTYPE html>
<html lang="en">
<head>
<meta charset="utf-8">
<title>Cedar Ridge Mechanical – Business Card</title>
<link rel="stylesheet" href="https://fonts.googleapis.com/css2?family=Montserrat:wght@300;400;500;700;800&display=swap">
<style>
  :root {
    --bg: #6e6e6e;
    --card-white: #ffffff;
    --card-black: #141414;
    --ink: #1b1b1b;
    --muted: #707070;
    --rule: #2a2a2a;
    --pattern-light: #2c2c2c;
    --pattern-dark: #0c0c0c;
  }
  * { box-sizing: border-box; margin: 0; padding: 0; }
  html, body { width: 1200px; height: 800px; overflow: hidden; }
  body {
    background: var(--bg);
    font-family: "Montserrat", sans-serif;
    display: flex;
    align-items: center;
    justify-content: center;
    gap: 50px;
  }
  .card {
    width: 525px;
    height: 300px;
    border-radius: 22px;
    position: relative;
    overflow: hidden;
    box-shadow: 0 14px 30px rgba(0,0,0,0.35);
  }
  /* Front */
  .card--front { background: var(--card-white); color: var(--ink); }
  .brand-name {
    position: absolute;
    left: 34px; top: 48px;
    width: 210px;
    font-weight: 700;
    font-size: 21px;
    line-height: 1.2;
    letter-spacing: 0.5px;
    text-transform: uppercase;
    color: var(--ink);
  }
  .contact-rule {
    position: absolute;
    left: 34px; top: 168px;
    width: 195px; height: 1px;
    background: var(--rule);
  }
  .contact-list {
    position: absolute;
    left: 34px; top: 182px;
    list-style: none;
    font-size: 13px;
    font-weight: 400;
    color: var(--muted);
    line-height: 22px;
  }
  .contact-list li { display: flex; align-items: center; gap: 9px; }
  .contact-list svg { width: 11px; height: 11px; fill: var(--ink); flex: none; }
  .person {
    position: absolute;
    right: 34px; top: 40px;
    text-align: right;
  }
  .person__name { font-weight: 800; font-size: 21px; letter-spacing: 0.3px; }
  .person__title { font-weight: 300; font-size: 14px; color: var(--muted); margin-top: 1px; }
  .person-rule {
    position: absolute;
    right: 34px; top: 98px;
    width: 210px; height: 1px;
    background: var(--rule);
  }
  .address {
    position: absolute;
    right: 34px; top: 112px;
    text-align: right;
    font-size: 13px;
    font-weight: 400;
    line-height: 21px;
    color: var(--muted);
  }
  .address strong { font-weight: 500; color: var(--ink); }
  /* Back */
  .card--back { background: var(--card-black); }
  .back-texture {
    position: absolute; inset: 0;
    background: linear-gradient(120deg, var(--pattern-dark) 0%, var(--pattern-light) 60%, #3a3a3a 100%);
  }
  .back-brand {
    position: absolute;
    left: 50%; top: 50%;
    transform: translate(-50%, -50%);
    color: #ffffff;
    font-weight: 700;
    font-size: 20px;
    letter-spacing: 1px;
    text-transform: uppercase;
    text-align: center;
    white-space: nowrap;
  }
</style>
</head>
<body>
  <section class="card card--front">
    <div class="brand-name">Cedar Ridge Mechanical</div>
    <div class="contact-rule"></div>
    <ul class="contact-list">
      <li><svg viewBox="0 0 24 24"><path d="M6.6 10.8a15 15 0 0 0 6.6 6.6l2.2-2.2c.3-.3.7-.4 1-.2 1.1.4 2.3.6 3.6.6.6 0 1 .4 1 1V20c0 .6-.4 1-1 1A17 17 0 0 1 3 4c0-.6.4-1 1-1h3.5c.6 0 1 .4 1 1 0 1.3.2 2.5.6 3.6.1.3 0 .7-.2 1z"/></svg>1-866-555-0148 Toll Free</li>
      <li><svg viewBox="0 0 24 24"><path d="M6.6 10.8a15 15 0 0 0 6.6 6.6l2.2-2.2c.3-.3.7-.4 1-.2 1.1.4 2.3.6 3.6.6.6 0 1 .4 1 1V20c0 .6-.4 1-1 1A17 17 0 0 1 3 4c0-.6.4-1 1-1h3.5c.6 0 1 .4 1 1 0 1.3.2 2.5.6 3.6.1.3 0 .7-.2 1z"/></svg>213-555-0192</li>
      <li><svg viewBox="0 0 24 24"><path d="M2 5h20v14H2zM3.5 6.5 12 13l8.5-6.5"/></svg>info@cedarridgemech.com</li>
      <li><svg viewBox="0 0 24 24"><circle cx="12" cy="12" r="10"/></svg>www.cedarridgemech.com</li>
    </ul>
    <div class="person">
      <div class="person__name">MARCUS WHITFIELD</div>
      <div class="person__title">President</div>
    </div>
    <div class="person-rule"></div>
    <div class="address">
      4127 Harbor Point Drive<br>
      Suite 210, Tustin, CA 92780<br>
      <strong>Mailing:</strong> 2260 Lakeview Ave. N,<br>
      Suite #417 Tacoma, WA 98402
    </div>
  </section>

  <section class="card card--back">
    <div class="back-texture" role="img" aria-label="Repeating brand emblem pattern in glossy black on matte black"></div>
    <div class="back-brand">Cedar Ridge Mechanical</div>
  </section>
</body>
</html>
```